Mortgage Broking Flyer to attract attention

We are looking for double sided, colour DL sized flyers for a mail drop to inform people what services we offer.
We are a Mortgage Broking Business in Alice Springs NT Australia. Alice Springs is a large country town so we want something that is personal, a little bit playful but still professional, and is going to capture the attention of potential clients when they first look at it so they want to read on.
Please use our logo and colours (red & white) plus a photo of our team – all attached.
Brochure Front: IMPORTANT
Please come up with a tag line based on the following-We want to be seen as different to the bank, more friendly, personable, we listen, want to help and want people to keep coming back even for the little things.
The home page from our website has good dot points but we would like them shorter and to the point www.ochrecrestlending.com.au
Plus include something which lets customer know that we can assist purchases made through any real estate office, anywhere in Australia
Don’t want the front to contain too many long sentences or paragraphs.
Brochure Back:
Please include:
Services/Specialties
• First home buyers
• Refinancing
• Investments
• Construction loans
• Debt consolidation
• Commercial finance
Please include the following contact details:
Dominic Farrow – Managing Director
Prudence Wexley – Loans Consultant
Maeve Dunleavy – Loans Consultant
Suite 4/17 Corbel Street, Alice Springs NT 0870
Phone: 08 8961 4728
www.ochrecrestlending.com.au
We must include the following fine print at the back/bottom of the brochure:
Dominic Farrow (Credit Representative Number: 527814), Prudence Wexley (Credit Representative Number: 527813) and Maeve Dunleavy (Credit Representative Number: 613290) are credit representatives of QMTRV Pty Ltd (Australian Credit Licence Number: 458906)
Please feel free to email me with any questions.
maeve@ochrecrestlending.com.au

```html
<!DOCTYPE html>
<html lang="en">
<head>
<meta charset="utf-8">
<title>Ochrecrest Lending – DL Flyer Front</title>
<link href="https://fonts.googleapis.com/css2?family=Roboto+Condensed:wght@300;400;700&family=Archivo:wght@800&display=swap" rel="stylesheet">
<style>
  :root {
    --brand-red: #e3202b;
    --deep-red: #8d0a12;
    --blush: #fbe3e5;
    --paper: #ffffff;
    --backdrop: #eef0f1;
    --photo-light: #eceae8;
  }
  * { margin: 0; padding: 0; box-sizing: border-box; }
  html, body { width: 1200px; height: 1000px; overflow: hidden; background: var(--backdrop); }
  .flyer {
    position: absolute; left: 385px; top: 50px;
    width: 430px; height: 900px;
    background: var(--paper);
    overflow: hidden;
    font-family: "Roboto Condensed", "Arial Narrow", sans-serif;
    box-shadow: 0 2px 10px rgba(0,0,0,0.08);
  }
  .hero-photo {
    position: absolute; left: 0; top: 90px; width: 430px; height: 340px;
    background: linear-gradient(90deg, var(--photo-light) 0%, #f4f1ef 30%, #c8343b 62%, var(--deep-red) 80%, #b3121c 100%);
    border-bottom-right-radius: 40px;
  }
  .header {
    position: absolute; left: 0; top: 0; width: 430px; height: 150px;
    background: var(--brand-red);
    border-bottom-left-radius: 55px;
    display: flex; align-items: center; padding: 0 24px 34px;
  }
  .brand-mark {
    width: 56px; height: 56px; border-radius: 50%; background: var(--paper); flex: none;
  }
  .brand-name {
    margin-left: 18px; color: var(--paper);
    font-weight: 300; font-size: 29px; letter-spacing: 0.5px; text-transform: uppercase;
  }
  .tagline {
    position: absolute; left: 248px; top: 228px;
    color: var(--paper); font-family: "Archivo", "Arial Black", sans-serif;
    font-weight: 800; font-size: 21px; line-height: 1.15; text-transform: uppercase;
  }
  .waves { position: absolute; left: 0; top: 400px; width: 430px; height: 340px; }
  .benefits {
    position: absolute; left: 28px; top: 458px; list-style: none;
    color: var(--brand-red); font-size: 29px; font-weight: 300; line-height: 1.17; text-transform: uppercase;
  }
  .benefits .num { font-weight: 700; margin-right: 12px; }
  .reach {
    position: absolute; left: 0; top: 730px; width: 430px; height: 170px;
    background: var(--brand-red); color: var(--paper);
    padding: 30px 28px 0; font-size: 23px; font-weight: 300; line-height: 1.2;
  }
  .reach strong { font-weight: 700; font-size: 30px; }
</style>
</head>
<body>
  <article class="flyer">
    <div class="hero-photo" role="img" aria-label="Photo of a smiling consultant holding a small model house against a red background"></div>
    <header class="header">
      <span class="brand-mark"></span>
      <span class="brand-name">Ochrecrest Lending</span>
    </header>
    <p class="tagline">We are<br>different<br>from banks</p>

    <svg class="waves" viewBox="0 0 430 340" aria-hidden="true">
      <path d="M0 0 C120 40 300 70 430 120 L430 140 C300 90 120 60 0 30 Z" fill="var(--blush)"/>
      <path d="M0 250 C150 270 300 300 430 340 L0 340 Z" fill="var(--blush)" opacity="0.7"/>
    </svg>

    <ol class="benefits">
      <li><span class="num">01</span>We are friendly...</li>
      <li><span class="num">02</span>Personable...</li>
      <li><span class="num">03</span>We listen...</li>
      <li><span class="num">04</span>Want to help</li>
      <li><span class="num">05</span>Want you coming back...</li>
    </ol>

    <section class="reach">
      <p>We can assist purchases made through any real estate office,<br>Anywhere in <strong>Australia</strong></p>
    </section>
  </article>
</body>
</html>
```